Employment Agency Website Design

We are working with an employment agency in California.

Some sites to use for content/competitors and inspiration:

https://www.pinecrestjobs.com/us/en
https://www.velmorusa.com
https://www.dravenworks.us
https://www.quillora.com/en
https://www.tomvalusa.com
https://www.fernstaffing.com

Thank you for taking the time to consider designing a website for us. We are web developers based in Stockton, CA, USA. Most of our projects go through the same process. Understanding this process may help you win a project with us. We custom-code all of our websites in-house. We don’t have any requirements as to what tools you use for your design, but we prefer Figma files. For any design that we label as four-stars, we send it to the client for review. The client picks the final design they want us to use. Once we complete this process, we will continue to show additional clients all the four-star sites and purchase them later. Your designs will have multiple chances to sell. For better chances of success, we ask that you follow these guidelines.

IMAGES:
If you use any images or icons in the design, we ask that you have a link to the asset so we can purchase the image/icon. Most of the designs we submit do not have the customer’s images on them unless they have some great images. Be creative; show us the feeling you are trying to portray with your image choices. Use any royalty-free site you choose. We subscribe to Adobe and mainly use their images, but we can purchase images outside of Adobe. PLEASE NOTE: we will not submit designs to clients with watermarks on the images.

FONTS:
We ask that you identify the fonts used in the design. This can be done in a message if you want. We typically use Google Fonts and Adobe Fonts.

CONTENT:
We're always open to different content and ideas. We often submit designs with stock images so the client can see our vision. We typically take pictures after the website launch to use their images with our vision. Lorem Ipsum is fine for paragraphs, but we ask that you write the headers in correct English. We want to be able to show the vision and identify the sections of the website.

INSPIRATION:
We typically add a couple of links in the brief of websites we like to help you get started in your design.

REVISIONS:
We do not often ask for revisions of the designs unless we see something in the design that may not appeal to the client. If there are slight changes that we want to make, we do that in the development process.

FEEDBACK:
We rarely give feedback on designs during the design process. We are working on many website projects and do not have the time to provide feedback. We usually respond if your request is well thought out and asks specific questions, but a note asking “feedback, please” usually goes unanswered.

```html
<!DOCTYPE html>
<html lang="en">
<head>
<meta charset="utf-8">
<title>Brightpath Talent – Grow With Us</title>
<link rel="stylesheet" href="https://fonts.googleapis.com/css2?family=Inter:wght@400;500;600;700&display=swap">
<style>
:root{
  --red:#be1e2d;
  --ink:#111111;
  --text:#3a3a3a;
  --muted:#6b6b6b;
  --page:#fafafa;
  --hero:#f8f1f1;
  --card:#ffffff;
  --line:#ececec;
  --dark:#0d0d0d;
}
*{box-sizing:border-box;margin:0;padding:0}
html,body{width:1200px;height:2455px;overflow:hidden}
body{background:var(--page);font-family:"Inter",sans-serif;color:var(--ink);position:relative}
a{color:inherit;text-decoration:none}
.accent{color:var(--red)}

/* header */
.site-header{position:absolute;top:0;left:0;width:1200px;height:78px;display:flex;align-items:center;padding:0 43px 0 52px;background:#fff}
.brand{display:flex;align-items:center;gap:6px;font-size:23px;font-weight:500;color:var(--red);width:300px}
.brand-mark{width:20px;height:20px;background:var(--red);border-radius:4px}
.main-nav{display:flex;gap:47px;font-size:17px;margin-left:57px}
.main-nav a.active{color:var(--red)}
.auth{margin-left:auto;display:flex;align-items:center;gap:17px;font-size:17px}
.auth .sign-in{color:#8a8a8a}
.btn-solid{background:var(--red);color:#fff;border-radius:8px;padding:10px 26px;font-weight:600}

/* hero */
.hero{position:absolute;top:78px;left:0;width:1200px;height:441px;background:var(--hero)}
.hero-photo{position:absolute;right:0;top:0;width:645px;height:441px;background:linear-gradient(90deg,#f3eeee 0%,#d9d5d2 25%,#b9b2ad 55%,#8c3a3d 75%,#4a4a4c 100%)}
.hero-copy{position:absolute;left:43px;top:60px;width:520px}
.hero-copy h1{font-size:54px;line-height:71px;font-weight:700;letter-spacing:-.3px;white-space:nowrap}
.hero-copy p{margin-top:30px;font-size:15px;line-height:23px;color:var(--text);width:430px}
.hero-actions{margin-top:25px;display:flex;align-items:center;gap:38px}
.btn-hire{background:var(--red);color:#fff;font-size:13.5px;font-weight:600;padding:14px 23px;border-radius:6px;letter-spacing:.2px}
.link-arrow{display:flex;align-items:center;gap:10px;font-size:14px;font-weight:500;text-decoration:underline}

/* section heads */
.eyebrow{font-size:17px;color:var(--text)}
.section-title{font-size:31px;font-weight:600;margin-top:10px;white-space:nowrap}
.see-all{position:absolute;right:50px;display:flex;align-items:center;gap:12px;font-size:17px;text-decoration:underline;color:#333;white-space:nowrap}

/* jobs */
.jobs{position:absolute;top:575px;left:43px;width:1157px}
.jobs .see-all{top:25px}
.job-row{position:absolute;top:88px;left:0;display:flex;gap:15px;width:1300px}
.job-card{width:317px;height:251px;background:var(--card);border:1px solid var(--line);border-radius:14px;padding:30px 32px;flex:none}
.job-top{display:flex;align-items:center;font-size:17px}
.job-top .company{display:flex;align-items:center;gap:11px;font-weight:500}
.job-top .sq{width:23px;height:23px;background:var(--red);border-radius:4px}
.job-top .type{margin-left:auto;color:var(--muted)}
.job-card h3{font-size:24px;font-weight:600;margin-top:36px;white-space:nowrap}
.job-card p{font-size:11.5px;line-height:15px;color:var(--text);margin-top:14px;width:240px}
.job-foot{display:flex;align-items:center;margin-top:35px}
.price{font-size:24px;font-weight:700}
.price small{font-size:11px;font-weight:400;margin-left:4px}
.btn-outline{margin-left:auto;border:1px solid #333;border-radius:6px;font-size:11.5px;padding:7px 15px;background:#fff}

/* service */
.service{position:absolute;top:965px;left:0;width:1200px}
.photo{position:absolute;border-radius:16px}
.photo.main{left:63px;top:0;width:547px;height:257px;background:linear-gradient(110deg,#e9ece6 0%,#b53035 40%,#e8e4e0 62%,#2e2e30 100%)}
.photo.left{left:63px;top:265px;width:273px;height:215px;background:linear-gradient(120deg,#dcdcd8,#a8302f 45%,#c7c2bb 75%,#8a6a4c)}
.photo.right{left:346px;top:265px;width:264px;height:215px;background:linear-gradient(120deg,#e5e3df,#b0262f 55%,#c9a27a)}
.service-copy{position:absolute;left:667px;top:8px;width:480px}
.service-copy h2{font-size:41px;line-height:58px;font-weight:700;white-space:nowrap;letter-spacing:-.2px}
.service-copy > p{font-size:15.5px;line-height:22px;color:var(--text);margin-top:10px;width:465px}
.feature{position:absolute;left:667px;width:458px;height:119px;background:#fff;border:1px solid var(--line);border-radius:12px;padding:22px 26px 0 18px;display:flex;gap:9px}
.feature h4{font-size:17px;font-weight:600}
.feature p{font-size:13px;line-height:16px;color:var(--text);margin-top:9px}
.feature svg{flex:none;margin-top:4px}

/* tips */
.tips{position:absolute;top:1518px;left:43px;width:1157px}
.tips .see-all{top:25px}
.blog-row{position:absolute;top:88px;left:0;display:flex;gap:11px;width:1400px}
.blog-card{width:442px;height:216px;background:#fff;border:1px solid var(--line);border-radius:14px;padding:30px 32px;flex:none}
.blog-card h3{font-size:24px;line-height:29px;font-weight:600;white-space:nowrap}
.blog-card p{font-size:11.5px;line-height:15px;color:var(--text);margin-top:14px;width:380px}
.blog-card .btn-outline{display:inline-block;margin-top:33px;margin-left:0}

/* benefits band */
.benefits{position:absolute;top:1867px;left:0;width:1200px;height:312px;background:var(--red);color:#fff}
.benefit-cols{display:flex;justify-content:space-between;padding:40px 40px 0 40px}
.benefit{width:340px;text-align:center}
.benefit h3{font-size:31px;font-weight:600;white-space:nowrap}
.benefit p{font-size:20px;line-height:24px;margin:12px auto 0;font-weight:400;width:320px}
.btn-ghost{position:absolute;left:466px;top:227px;width:268px;height:46px;border:1px solid #fff;border-radius:8px;display:flex;align-items:center;justify-content:center;font-size:14px;font-weight:500}

/* footer */
.site-footer{position:absolute;top:2179px;left:0;width:1200px;height:241px;background:var(--page)}
.footer-brand{position:absolute;left:86px;top:42px}
.footer-brand p{font-size:13.5px;line-height:20px;color:var(--text);margin-top:22px;width:235px}
.footer-col{position:absolute;top:42px}
.footer-col h5{font-size:19px;font-weight:600;margin-bottom:22px;white-space:nowrap}
.footer-col li{list-style:none;font-size:13.5px;line-height:26.5px;color:#222;white-space:nowrap}
.copyright{position:absolute;top:2420px;left:0;width:1200px;height:35px;background:var(--dark);color:#fff;font-size:13.5px;display:flex;align-items:center;justify-content:center}
</style>
</head>
<body>

<header class="site-header">
  <a class="brand" href="#"><span class="brand-mark"></span>brightpath</a>
  <nav class="main-nav">
    <a class="active" href="#">Home</a>
    <a href="#">Services</a>
    <a href="#">Category</a>
    <a href="#">Blog</a>
    <a href="#">About Us</a>
  </nav>
  <div class="auth">
    <a class="sign-in" href="#">Sign In</a>
    <a class="btn-solid" href="#">Sign Up</a>
  </div>
</header>

<section class="hero">
  <div class="hero-photo" role="img" aria-label="Two smiling businesswomen in red and grey blazers reviewing a document in a bright office"></div>
  <div class="hero-copy">
    <h1>Grow With Us And<br><span class="accent">Build</span> Your Career</h1>
    <p>We are committed to providing a work environment that supports individual growth, enables employees to sharpen their skills, and achieve their maximum potential</p>
    <div class="hero-actions">
      <a class="btn-hire" href="#">HIRE EXPERT TALENT</a>
      <a class="link-arrow" href="#">Apply for a job
        <svg width="9" height="14" viewBox="0 0 9 14"><path d="M2 2l5 5-5 5" fill="none" stroke="#111" stroke-width="1.8"/></svg></a>
    </div>
  </div>
</section>

<section class="jobs">
  <p class="eyebrow">999+ Jobs uploaded per day</p>
  <h2 class="section-title">Explore <span class="accent">Job and Talent</span> Everywhere</h2>
  <a class="see-all" href="#">See All Job <svg width="8" height="14" viewBox="0 0 8 14"><path d="M1.5 2l5 5-5 5" fill="none" stroke="#333" stroke-width="1.6"/></svg></a>
  <div class="job-row">
    <article class="job-card">
      <div class="job-top"><span class="company"><span class="sq"></span>Corvix</span><span class="type">Full time</span></div>
      <h3>UI/UX Designer</h3>
      <p>Lorem Ipsum is simply dummy text of the printing and typesetting industry.....</p>
      <div class="job-foot"><span class="price">$240<small>/hour</small></span><a class="btn-outline" href="#">Apply Now</a></div>
    </article>
    <article class="job-card">
      <div class="job-top"><span class="company"><span class="sq"></span>Lumora</span><span class="type">Full time</span></div>
      <h3>Back-End Developer</h3>
      <p>Lorem Ipsum is simply dummy text of the printing and typesetting industry.....</p>
      <div class="job-foot"><span class="price">$240<small>/hour</small></span><a class="btn-outline" href="#">Apply Now</a></div>
    </article>
    <article class="job-card">
      <div class="job-top"><span class="company"><span class="sq"></span>Tallowy</span><span class="type">Full time</span></div>
      <h3>Front-End Developer</h3>
      <p>Lorem Ipsum is simply dummy text of the printing and typesetting industry.....</p>
      <div class="job-foot"><span class="price">$240<small>/hour</small></span><a class="btn-outline" href="#">Apply Now</a></div>
    </article>
    <article class="job-card">
      <div class="job-top"><span class="company"><span class="sq"></span>Orbisa</span><span class="type">Full time</span></div>
      <h3>Project Manager</h3>
      <p>Lorem Ipsum is simply dummy text of the printing and typesetting industry.....</p>
      <div class="job-foot"><span class="price">$240<small>/hour</small></span><a class="btn-outline" href="#">Apply Now</a></div>
    </article>
  </div>
</section>

<section class="service">
  <div class="photo main" role="img" aria-label="Two colleagues laughing together over a laptop in an office"></div>
  <div class="photo left" role="img" aria-label="Two women working side by side at a desk with laptop and notes"></div>
  <div class="photo right" role="img" aria-label="Woman in a red blazer writing notes beside a laptop"></div>
  <div class="service-copy">
    <h2><span class="accent">Our Service</span> To Provide<br>Your Career Grows</h2>
    <p>Empowering Your Career Journey: Our service is dedicated to fostering your professional growth, providing tailored support to ensure your success in every step of your career</p>
  </div>
  <div class="feature" style="top:222px">
    <svg width="16" height="14" viewBox="0 0 16 14"><path d="M2 2l5 5-5 5M8 2l5 5-5 5" fill="none" stroke="#be1e2d" stroke-width="1.6"/></svg>
    <div><h4>Personalized Career Guidance</h4><p>Our service offers personalized guidance to help you navigate your career path effectively. Through tailored advice, mentorship, and resources</p></div>
  </div>
  <div class="feature" style="top:355px">
    <svg width="16" height="14" viewBox="0 0 16 14"><path d="M2 2l5 5-5 5M8 2l5 5-5 5" fill="none" stroke="#be1e2d" stroke-width="1.6"/></svg>
    <div><h4>Skill Development Hub</h4><p>Elevate your career prospects with our skill development hub. Gain access to curated courses, workshops, and resources designed to enhance your skill set and keep you competitive</p></div>
  </div>
</section>

<section class="tips">
  <p class="eyebrow">Tips and Tricks</p>
  <h2 class="section-title">Find <span class="accent">Information</span> to Help and Make you Grow</h2>
  <a class="see-all" href="#">See All Blog <svg width="8" height="14" viewBox="0 0 8 14"><path d="M1.5 2l5 5-5 5" fill="none" stroke="#333" stroke-width="1.6"/></svg></a>
  <div class="blog-row">
    <article class="blog-card">
      <h3>The Secret to Successfully<br>Recruiting Quality Employees</h3>
      <p>Lorem Ipsum is simply dummy text of the printing and typesetting industry.....</p>
      <a class="btn-outline" href="#">Read Now</a>
    </article>
    <article class="blog-card">
      <h3>Quick Guide to Uncovering<br>Hidden Talents</h3>
      <p>Lorem Ipsum is simply dummy text of the printing and typesetting industry.....</p>
      <a class="btn-outline" href="#">Read Now</a>
    </article>
    <article class="blog-card">
      <h3>Smart Navigation in the World<br>of Recruitment</h3>
      <p>Lorem Ipsum is simply dummy text of the printing and typesetting industry.....</p>
      <a class="btn-outline" href="#">Read Now</a>
    </article>
  </div>
</section>

<section class="benefits">
  <div class="benefit-cols">
    <div class="benefit"><h3>Benefit? Absolutely</h3><p>Secure a temporary position through us, and unlock a range of attractive advantages.</p></div>
    <div class="benefit"><h3>Why Temporary?</h3><p>Quality positions with reputable organizations. Is opting for temporary work the suitable decision for you</p></div>
    <div class="benefit"><h3>Flexibility? Indeed</h3><p>Temporary jobs offer the flexibility to accommodate your lifestyle and career goals.</p></div>
  </div>
  <a class="btn-ghost" href="#">Learn More About Us</a>
</section>

<footer class="site-footer">
  <div class="footer-brand">
    <a class="brand" href="#"><span class="brand-mark"></span>brightpath</a>
    <p>Personal growth, honing skills, and unlocking employees' full potential in our supportive work environment</p>
  </div>
  <div class="footer-col" style="left:502px"><h5>Information</h5><ul><li>Privacy Policy</li><li>Payment Method</li><li>Refund Policy</li><li>Terms of use</li></ul></div>
  <div class="footer-col" style="left:667px"><h5>Services</h5><ul><li>Privacy Policy</li><li>Payment Method</li><li>Refund Policy</li><li>Shopping</li></ul></div>
  <div class="footer-col" style="left:835px"><h5>Navigation</h5><ul><li>Home</li><li>Category</li><li>Service</li><li>Profile</li></ul></div>
  <div class="footer-col" style="left:991px"><h5>Our Company</h5><ul><li>About Us</li><li>Contact Information</li></ul></div>
</footer>
<div class="copyright">@ Copyright 2024 Brightpath Talent</div>

</body>
</html>
```